"Harbor Builders" is a residential building company and needs a new business card design and may re

We would like a redesign based on the existing logo, and would like to see a new font as well. We are bespoke home builders who build sustainable energy efficient homes.

Industry/Entity Type

Construction

Contact Information for Business Card

Business card size 40mm x 90mm

Colors

Designer to choose colors to be used in the design.

```html
<!DOCTYPE html>
<html lang="en">
<head>
<meta charset="utf-8">
<title>Harbor Builders – Business Card</title>
<link rel="stylesheet" href="https://fonts.googleapis.com/css2?family=Figtree:wght@400;500;700&display=swap">
<style>
  :root {
    --paper: #ffffff;
    --ink: #111111;
    --brand-yellow: #fdd54e;
    --pattern-tone: #3a3a3a;
    --rule: #222222;
  }
  * { margin: 0; padding: 0; box-sizing: border-box; }
  html, body {
    width: 1200px; height: 1200px; overflow: hidden;
    background: var(--paper);
    font-family: "Figtree", Arial, sans-serif;
    color: var(--ink);
  }
  .canvas { position: relative; width: 1200px; height: 1200px; }

  .card {
    position: absolute;
    left: 146px; width: 909px; height: 413px;
    border: 1.5px solid var(--ink);
    background: var(--paper);
    overflow: hidden;
  }
  .card--front { top: 162px; }
  .card--back  { top: 640px; height: 404px; }

  .front-pattern {
    position: absolute; inset: 0;
    background: var(--pattern-tone);
  }
  .front-badge {
    position: absolute;
    left: 299px; top: 50px;
    width: 309px; height: 309px;
    background: var(--paper);
    border: 1.5px solid var(--ink);
    display: flex; flex-direction: column;
    align-items: center; justify-content: center;
    color: var(--brand-yellow);
    font-weight: 500;
  }
  .front-badge__mark {
    width: 110px; height: 110px;
    background: var(--brand-yellow);
    margin-bottom: 26px;
  }
  .front-badge__name { font-size: 50px; line-height: 1; letter-spacing: -1.5px; }
  .front-badge__sub  { font-size: 34px; line-height: 1.1; letter-spacing: -0.5px; }

  .back-mark {
    position: absolute;
    left: 40px; top: 62px;
    width: 280px; height: 280px;
    background: var(--brand-yellow);
  }
  .contact { position: absolute; left: 442px; top: 0; width: 440px; }
  .contact__line { position: absolute; left: 0; white-space: nowrap; font-size: 24px; line-height: 1; }
  .contact__company { top: 81px; }
  .contact__name { top: 152px; font-weight: 700; }
  .contact__phone { top: 186px; letter-spacing: 0.5px; }
  .contact__email { top: 226px; }
  .contact__reg { top: 300px; }
  .contact__rule {
    position: absolute; left: 0; width: 428px; height: 1px;
    background: var(--rule);
  }
  .contact__rule--top { top: 130px; }
  .contact__rule--bottom { top: 280px; }
</style>
</head>
<body>
<main class="canvas">
  <section class="card card--front">
    <div class="front-pattern" role="img" aria-label="Repeating pattern of textured black brand marks on white"></div>
    <div class="front-badge">
      <div class="front-badge__mark"></div>
      <span class="front-badge__name">Harbor</span>
      <span class="front-badge__sub">Builders</span>
    </div>
  </section>

  <section class="card card--back">
    <div class="back-mark"></div>
    <div class="contact">
      <p class="contact__line contact__company">Harbor Builders Pty Ltd</p>
      <div class="contact__rule contact__rule--top"></div>
      <p class="contact__line contact__name">Daniel Moretti</p>
      <p class="contact__line contact__phone">0400 555 018</p>
      <p class="contact__line contact__email">daniel@harborbuilders.com.au</p>
      <div class="contact__rule contact__rule--bottom"></div>
      <p class="contact__line contact__reg">Registration 40381 ABN: 12 345 678 901</p>
    </div>
  </section>
</main>
</body>
</html>
```